Biz Card

MARKETING today is the most rapidly changing business discipline. Media options to reach customers, actual customer preferences and consumer buying decisions change by the minute . . . no, by the second. The behavioral data generated by all aspects of the business and the new technologies that put the data to work together produce the potential to generate business intelligence and guide smart resource allocation to influence purchase and retention. However, to realize this potential, marketing professionals at all levels and in all organizations must continuously improve their skills not just from on-the-job training but by learning from masters in the field. The Bright Horizon Guild is the training center that serves this professional development need.model logos:msi.orgama.orgcontentmarketinginstitute.comBook covers on MarketingMetrics, Marketing Anaytics
Industry/Entity Type
Business
Contact Information for Business Card
Roy A. YoungCEOMarketing Science Academyphone: 310-601-4755email: roy@marketingscience.comAddress:437 South Rexford DriveBeverly Hills, CA 89377
Look and feel
Each slider illustrates characteristics of the customer's brand and the style your logo design should communicate.

```html
<!DOCTYPE html>
<html lang="en">
<head>
<meta charset="utf-8">
<title>Bright Horizon Guild – Business Card</title>
<link href="https://fonts.googleapis.com/css2?family=Jost:wght@400;600&display=swap" rel="stylesheet">
<style>
  :root {
    --navy: #243a7e;
    --red: #c1272d;
    --grey-band: #c4c4c4;
    --ink: #3a3a3a;
    --paper: #ffffff;
    --backdrop: #e9e9e9;
  }
  html, body {
    margin: 0;
    width: 1200px;
    height: 900px;
    overflow: hidden;
    background: var(--backdrop);
    font-family: "Jost", Arial, sans-serif;
  }
  .business-card {
    position: absolute;
    left: 100px;
    top: 165px;
    width: 1000px;
    height: 571px;
    background: var(--paper);
    overflow: hidden;
    box-shadow: 0 6px 24px rgba(0,0,0,0.12);
  }
  .card-bands {
    position: absolute;
    inset: 0;
    width: 1000px;
    height: 571px;
  }
  .brand-mark {
    position: absolute;
    left: 62px;
    top: 78px;
    display: flex;
    align-items: center;
    gap: 14px;
  }
  .brand-square {
    width: 30px;
    height: 30px;
    background: var(--red);
  }
  .brand-name {
    font-weight: 600;
    font-size: 36px;
    color: var(--navy);
    letter-spacing: 0.5px;
  }
  .holder {
    position: absolute;
    left: 700px;
    top: 150px;
    color: var(--ink);
    font-size: 26px;
    line-height: 1.15;
  }
  .contact-block {
    position: absolute;
    left: 92px;
    top: 255px;
    color: var(--ink);
  }
  .company-name {
    margin: 0 0 4px;
    font-weight: 400;
    font-size: 42px;
    color: var(--navy);
    line-height: 1.05;
  }
  .address {
    margin: 0;
    font-size: 21px;
  }
  .contact-line {
    margin: 2px 0 0;
    font-size: 21px;
    display: flex;
    align-items: center;
    gap: 8px;
  }
  .contact-line .gap { width: 14px; }
  .icon { width: 16px; height: 14px; }
</style>
</head>
<body>
  <section class="business-card">
    <svg class="card-bands" viewBox="0 0 1000 571" aria-hidden="true">
      <path fill="var(--grey-band)" d="M0,385 L640,495 L790,400 L1000,345 L1000,571 L0,571 Z"/>
      <path fill="var(--red)" d="M0,410 L620,508 L680,508 L810,412 L1000,365 L1000,571 L0,571 Z"/>
      <path fill="var(--navy)" d="M330,571 L720,548 L1000,440 L1000,571 Z"/>
    </svg>

    <div class="brand-mark">
      <span class="brand-square"></span>
      <span class="brand-name">Bright Horizon Guild</span>
    </div>

    <div class="holder">
      <div class="holder-name">Neil P. Barton</div>
      <div class="holder-title">CEO</div>
    </div>

    <div class="contact-block">
      <h1 class="company-name">Bright Horizon Guild</h1>
      <p class="address">912 North Calloway Lane.&nbsp; Beverly Hills, CA 89377</p>
      <p class="contact-line">
        <svg class="icon" viewBox="0 0 16 14" aria-hidden="true"><path fill="var(--red)" d="M1,5 Q8,-1 15,5 L13,7 L11,5 L5,5 L3,7 Z M3,8 L13,8 L14,13 L2,13 Z"/></svg>
        <span>310-555-0182</span>
        <span class="gap"></span>
        <svg class="icon" viewBox="0 0 16 14" aria-hidden="true"><rect x="1" y="2" width="14" height="10" fill="var(--red)"/><path d="M1,2 L8,8 L15,2" stroke="#fff" stroke-width="1.4" fill="none"/></svg>
        <span>neil@brighthorizonguild.com</span>
      </p>
    </div>
  </section>
</body>
</html>
```